3D abstract logo Construction, Kitchen and Bath design and Project Management Business Card Design

I want a 3d abstract logo for a new General Construction, Kitchen and Bath design and Project Management Company located at Philadelphia PA, we want to put our logo in the white color trucks too. I want to look professional and serious at the same time look like an architect design and the warm originals color that make you feel in a nice decorated home, I like the colors trend in this link:
http://www.quellmark.example/qm/ggs/pageeditor.aspx?alt_doc_id=RT41K-M9B33-2W5&doc_id=5913046628&pf_id=D4H

I was thinking about a roof and the PA font could have square shape or like wood framing with two tones of the brick color black and creamy yellow color.... Also I like the keystone Idea like the modification or the Ridgeline Parkway logo but curvy at the top

The final design should communicate big company (because we want to grow), responsible, professional and organized that really care about our customers and give them everything they need... plan and design, excellent labor and Project Management
Updates

I doesn't have to be 3d

Reason: I haven't received enough options...

Please stick with the warm tones shown in the image001 attached I like spicy cinnamon instead a cold wine or brick color and also the cream yellowish tones added

Hello designers, please use only the idea and colors of the image001 I don't want to be stick with a house logo because I do commercial construction too so I prefer work around the keystone idea maybe leaving the style of the PA.
I'd like the base tone on the card dark like first option and you can send me a white option too.

Please send me your ideas as soon as possible 

Thank you so much!

Target Market(s)

Builders, State, commercial business owners, Property owners or Real State and Property Management Companies

Industry/Entity Type

Architect

Contact Information for Business Card

RK Buildworks LLC
“Your project is our business”
Lorna Vasquel Eng.
President
Commercial & Residential General Construction
Kitchen & Bath Design | Project Management
Phone: 555-304-7718 | Fax: 555-304-7719 Cell: 555-862-3097
lorna@rkbuildworks.example

```html
<!DOCTYPE html>
<html lang="en">
<head>
<meta charset="utf-8">
<title>RK Buildworks – Business Cards</title>
<link rel="stylesheet" href="https://fonts.googleapis.com/css2?family=Arimo:ital,wght@0,400;0,700;1,400&family=Open+Sans:wght@400&display=swap">
<style>
  :root {
    --cinnamon: #7a211d;
    --cream: #f1ecdc;
    --cream-warm: #f7e9d6;
    --rose: #b5625a;
    --tan: #d8b878;
    --brown: #8b5a3c;
    --ink: #1f1f1f;
    --page: #ffffff;
  }
  * { box-sizing: border-box; margin: 0; padding: 0; }
  html, body { width: 1200px; height: 959px; overflow: hidden; background: var(--page); }
  .stage {
    position: relative; width: 1127px; height: 900px;
    transform: scale(1.0648); transform-origin: 0 0;
    font-family: "Arimo", Arial, sans-serif;
  }
  .card { position: absolute; overflow: hidden; }
  .card--front { width: 554px; height: 325px; }
  .card--back { width: 324px; height: 553px; text-align: center; }
  .card--light { background: var(--cream); color: var(--cinnamon); }
  .card--dark { background: var(--cinnamon); color: var(--cream-warm); }
  .front-light { left: 0; top: 0; }
  .front-dark { left: 578px; top: 1px; }
  .back-light { left: 102px; top: 342px; }
  .back-dark { left: 680px; top: 344px; }

  .card__art { position: absolute; inset: 0; width: 100%; height: 100%; }
  .holder { position: absolute; left: 27px; top: 26px; }
  .holder__name { font-size: 28px; font-weight: 700; letter-spacing: .3px; line-height: 1; }
  .holder__title { font-size: 18px; font-style: italic; margin-top: 6px; }
  .services {
    position: absolute; left: 27px; top: 105px;
    font-family: "Open Sans", Verdana, sans-serif; font-size: 17.5px; line-height: 21px;
  }
  .card--light .services { color: var(--rose); }
  .contacts { position: absolute; left: 27px; top: 213px; font-size: 14px; line-height: 24.5px; }
  .contacts__row { display: flex; }
  .contacts__label { width: 77px; }
  .card--light .contacts__value { color: var(--ink); }

  .brand-badge {
    position: absolute; left: 408px; top: 184px; width: 110px; height: 110px;
    display: flex; flex-direction: column; align-items: center; justify-content: center;
    font-size: 13px; font-weight: 700; line-height: 16px; letter-spacing: .5px;
  }
  .card--light .brand-badge { color: var(--cinnamon); }
  .card--dark .brand-badge { color: var(--cream-warm); }

  .brand-name { margin-top: 276px; font-size: 26px; font-weight: 700; letter-spacing: 1px; }
  .tagline { margin-top: 16px; font-size: 18px; }
  .website { margin-top: 92px; font-size: 14px; }
</style>
</head>
<body>
<main class="stage">

  <section class="card card--front card--light front-light">
    <svg class="card__art" viewBox="0 0 554 325" aria-hidden="true">
      <path d="M478 0 C505 110 480 260 340 325 L554 325 L554 0 Z" fill="var(--cinnamon)"/>
      <path d="M462 0 C489 110 464 255 326 325" fill="none" stroke="var(--brown)" stroke-width="5"/>
      <path d="M470 0 C497 112 472 258 334 325" fill="none" stroke="var(--rose)" stroke-width="5"/>
      <path d="M487 0 C514 110 490 265 356 325" fill="none" stroke="var(--tan)" stroke-width="4"/>
      <path d="M496 0 C522 115 498 268 370 325" fill="none" stroke="var(--rose)" stroke-width="3"/>
      <circle cx="463" cy="239" r="55" fill="var(--cream)"/>
    </svg>
    <div class="holder">
      <h1 class="holder__name">LORNA VASQUEL</h1>
      <p class="holder__title">Eng. President</p>
    </div>
    <p class="services">Commercial &amp; Residential General<br>Construction Kitchen &amp; Bath Design</p>
    <dl class="contacts">
      <div class="contacts__row"><dt class="contacts__label">Phone:</dt><dd class="contacts__value">555-304-7718</dd></div>
      <div class="contacts__row"><dt class="contacts__label">Fax:</dt><dd class="contacts__value">555-304-7719</dd></div>
      <div class="contacts__row"><dt class="contacts__label">Cell:</dt><dd class="contacts__value">555-862-3097</dd></div>
      <div class="contacts__row"><dt class="contacts__label">Email:</dt><dd class="contacts__value">lorna@rkbuildworks.example</dd></div>
    </dl>
    <div class="brand-badge"><span>RK</span><span>BUILDWORKS</span></div>
  </section>

  <section class="card card--front card--dark front-dark">
    <svg class="card__art" viewBox="0 0 554 325" aria-hidden="true">
      <path d="M478 0 C505 110 480 260 340 325 L554 325 L554 0 Z" fill="var(--cream-warm)"/>
      <path d="M462 0 C489 110 464 255 326 325" fill="none" stroke="var(--brown)" stroke-width="5"/>
      <path d="M470 0 C497 112 472 258 334 325" fill="none" stroke="var(--rose)" stroke-width="5"/>
      <path d="M487 0 C514 110 490 265 356 325" fill="none" stroke="var(--tan)" stroke-width="4"/>
      <path d="M496 0 C522 115 498 268 370 325" fill="none" stroke="var(--rose)" stroke-width="3"/>
      <circle cx="461" cy="241" r="57" fill="var(--cinnamon)"/>
    </svg>
    <div class="holder">
      <h2 class="holder__name">LORNA VASQUEL</h2>
      <p class="holder__title">Eng. President</p>
    </div>
    <p class="services">Commercial &amp; Residential General<br>Construction Kitchen &amp; Bath Design</p>
    <dl class="contacts">
      <div class="contacts__row"><dt class="contacts__label">Phone:</dt><dd class="contacts__value">555-304-7718</dd></div>
      <div class="contacts__row"><dt class="contacts__label">Fax:</dt><dd class="contacts__value">555-304-7719</dd></div>
      <div class="contacts__row"><dt class="contacts__label">Cell:</dt><dd class="contacts__value">555-862-3097</dd></div>
      <div class="contacts__row"><dt class="contacts__label">Email:</dt><dd class="contacts__value">lorna@rkbuildworks.example</dd></div>
    </dl>
    <div class="brand-badge"><span>RK</span><span>BUILDWORKS</span></div>
  </section>

  <section class="card card--back card--light back-light">
    <p class="brand-name">RK BUILDWORKS</p>
    <p class="tagline">Your project is our business</p>
    <p class="website">www.rkbuildworks.example</p>
  </section>

  <section class="card card--back card--dark back-dark">
    <p class="brand-name">RK BUILDWORKS</p>
    <p class="tagline">Your project is our business</p>
    <p class="website">www.rkbuildworks.example</p>
  </section>

</main>
</body>
</html>
```